Redesign current business card for food company

i would like to redesign my business card. our company is food company, our product range from chips, juices, milk and etc (mostly dried food stuff).
I want o keep same logo but , the rest is open to new design.
you can check at our website about our company www.orvelpantry.com

Target Market(s)

most of food company

Industry/Entity Type

Business

Contact Information for Business Card

I want to keep more to blue color...

Colors
3176b5
abd036

Requirements
Must have
• our old logo
Nice to have
• we do not mind to have nice material on bus card in order to accomplish nice design. for example: using spot uv, embossed and etc.

```html
<!DOCTYPE html>
<html lang="en">
<head>
<meta charset="utf-8">
<title>Orvel Business Card</title>
<link rel="stylesheet" href="https://fonts.googleapis.com/css2?family=Montserrat:wght@400;500;600;700&display=swap">
<style>
  :root {
    --page: #e9e7e3;
    --white: #ffffff;
    --blue: #3b3ab2;
    --blue-deep: #2b2a93;
    --blue-light: #5858c4;
    --cyan: #1fb0cb;
    --green: #7fb43a;
    --ink: #34349f;
  }
  * { margin: 0; padding: 0; box-sizing: border-box; }
  html, body { width: 1200px; height: 913px; overflow: hidden; }
  body {
    background: var(--page);
    font-family: "Montserrat", Arial, sans-serif;
    position: relative;
  }
  .card {
    position: absolute;
    top: 302px;
    width: 540px;
    height: 309px;
    border-radius: 16px;
    overflow: hidden;
    box-shadow: 0 6px 18px rgba(0,0,0,0.18);
  }
  .card-front { left: 45px; background: var(--white); }
  .card-back {
    left: 615px;
    background: linear-gradient(160deg, var(--blue-light) 0%, var(--blue) 45%, var(--blue-deep) 100%);
  }
  .front-shapes { position: absolute; inset: 0; }

  .brand-name {
    position: absolute;
    left: 32px;
    top: 58px;
    font-size: 84px;
    font-weight: 600;
    letter-spacing: -2px;
    color: var(--ink);
    line-height: 1;
  }

  .person { position: absolute; left: 30px; top: 206px; }
  .person-name { font-size: 15px; font-weight: 700; color: var(--blue-deep); }
  .person-title { font-size: 11px; font-weight: 500; color: var(--white); margin-top: 1px; }

  .address {
    position: absolute;
    left: 44px;
    top: 245px;
    font-size: 12px;
    line-height: 15px;
    color: var(--white);
  }

  .contacts {
    position: absolute;
    right: 22px;
    top: 174px;
    list-style: none;
    text-align: right;
    font-size: 11.5px;
    line-height: 17px;
    color: var(--white);
  }
  .contacts li { display: flex; justify-content: flex-end; align-items: center; gap: 7px; }
  .contacts svg { width: 10px; height: 10px; flex: none; }

  .back-mark {
    position: absolute;
    left: 0; right: 0;
    top: 92px;
    text-align: center;
    font-size: 110px;
    font-weight: 600;
    letter-spacing: -3px;
    color: rgba(40, 38, 140, 0.55);
    line-height: 1;
  }
  .back-web {
    position: absolute;
    left: 0; right: 0;
    top: 232px;
    text-align: center;
    font-size: 15px;
    letter-spacing: 0.5px;
    color: var(--white);
  }
</style>
</head>
<body>

<section class="card card-front">
  <svg class="front-shapes" viewBox="0 0 540 309" aria-hidden="true">
    <polygon points="0,193 540,158 540,164 0,199" fill="var(--green)"/>
    <polygon points="0,199 540,164 540,309 0,309" fill="var(--blue)"/>
    <polygon points="0,199 335,177 305,240 0,240" fill="var(--cyan)"/>
  </svg>

  <div class="brand-name">orvel</div>

  <div class="person">
    <div class="person-name">Daniel Hartono</div>
    <div class="person-title">President</div>
  </div>

  <div class="address">
    Orvel Enterprises Corp.<br>
    2418 Meadow Ave.<br>
    Ontario CA 91761
  </div>

  <ul class="contacts">
    <li>555 210 4480
      <svg viewBox="0 0 10 10"><path d="M2 1l2 2-1 1.2c.6 1.2 1.6 2.2 2.8 2.8L7 6l2 2-1.4 1.4C4.5 9 1 5.5.6 2.4z" fill="#fff"/></svg>
    </li>
    <li>555 210 4481
      <svg viewBox="0 0 10 10"><rect x="1" y="3" width="8" height="5" rx="1" fill="#fff"/><rect x="3" y="1" width="4" height="2" fill="#fff"/></svg>
    </li>
    <li>555 873 2209
      <svg viewBox="0 0 10 10"><rect x="2.5" y="0.5" width="5" height="9" rx="1" fill="none" stroke="#fff"/></svg>
    </li>
    <li>daniel@orvelpantry.com
      <svg viewBox="0 0 10 10"><rect x="0.5" y="2" width="9" height="6" fill="none" stroke="#fff"/><path d="M0.5 2l4.5 3.5L9.5 2" fill="none" stroke="#fff"/></svg>
    </li>
    <li>www.orvelpantry.com
      <svg viewBox="0 0 10 10"><circle cx="5" cy="5" r="4.3" fill="none" stroke="#fff"/><path d="M0.7 5h8.6M5 0.7c-2.4 2.4-2.4 6.2 0 8.6M5 0.7c2.4 2.4 2.4 6.2 0 8.6" fill="none" stroke="#fff" stroke-width="0.8"/></svg>
    </li>
  </ul>
</section>

<section class="card card-back">
  <div class="back-mark">orvel</div>
  <div class="back-web">www.orvelpantry.com</div>
</section>

</body>
</html>
```